Cutting Edge Property Services Provider is Looking to Update Business Card Design

We are looking to freshen up our business cards to match our cutting edge technology based image.

KORVANEX - Where Care Finds Its Pulse

More information about our company can be found on our website at www.korvanex-demo.net

We integrate technology in a historically low tech industry.

We have appeared on the Brisk 300/3000 list 2 years in a row and we're previously recognized as the 5th Quickest Rising Firm in San Diego.

Our core colors are blue and white, but are not against accents that might improve our image.

We currently have our Mission Statement on our Business Cards in a folding design:
KORVANEX IS THE LEADING BUILDING SERVICES INNOVATOR. BY COMBINING TECHNOLOGY WITH FUNCTIONAL TOOS THAT IMPROVE EFFICIENCY IN THE WORKPLACE, WE PROVIDE UNPARALLELED SERVICE IN THE INDUSTRY. DEVELOPING LASTING RELATIONSHIPS WITH OUR CLIENTS AND ASSOCIATES IS THE CORNERSTONE OF OUR SUCCESS.

We'd like to convey the image of a cutting edge, technology based company. Want the cards to pop.

Target Market(s)

Commercial Property Managers - 20 to 50 year old professionals

Industry/Entity Type

Business

Requirements
Must have
• Must utilize our logo obviously, but are definitely open to using variations on the logo. Utilizing the components of the logo, but maybe in different configurations or backgrounds, etc...

Must use the Name: KORVANEX.
Can also use KORVANEX PROPERTY SERVICES.

Must include the Mission Statement

Must say: Where Care Finds Its Pulse
Nice to have
• We are considering plastic stock, shaped cards, or folding cards.

Nothing over the top or really expensive, but will consider if it conveys innovation and technology.
Should not have
• No images of toilets, buildings, trees, or anything relating to commercial properties.

We want to convey our technology image.

```html
<!DOCTYPE html>
<html lang="en">
<head>
<meta charset="utf-8">
<title>KORVANEX Business Card</title>
<link rel="stylesheet" href="https://fonts.googleapis.com/css2?family=Mulish:wght@400;600;800&display=swap">
<style>
  :root {
    --brand-blue: #0d4f7e;
    --band-blue: #0b4a78;
    --rule-grey: #b9c2cb;
    --card-face: #f1f3f5;
    --card-edge: #d6dbe0;
    --ink: #3a3f45;
    --paper: #e4e7ea;
    --white: #ffffff;
  }
  * { box-sizing: border-box; margin: 0; padding: 0; }
  html, body { width: 1200px; height: 900px; overflow: hidden; }
  body {
    position: relative;
    background: var(--paper);
    font-family: "Mulish", Arial, sans-serif;
    color: var(--ink);
  }
  .card {
    position: absolute;
    width: 560px;
    height: 320px;
    border-radius: 18px;
    background: var(--card-face);
    border: 1px solid var(--card-edge);
    box-shadow: 0 10px 30px rgba(0,0,0,0.10);
    overflow: hidden;
  }
  .card--front { left: 388px; top: 46px; }
  .card--back  { left: 225px; top: 408px; }

  .brand {
    position: absolute;
    left: 0; right: 0;
    display: flex;
    align-items: center;
    justify-content: center;
    gap: 12px;
  }
  .brand__mark {
    width: 30px; height: 30px;
    background: var(--brand-blue);
    border-radius: 5px;
  }
  .brand__name {
    font-weight: 800;
    font-size: 36px;
    letter-spacing: 1px;
    color: var(--brand-blue);
  }
  .card--front .brand { top: 80px; }
  .card--back .brand { top: 62px; }

  .rule {
    position: absolute;
    left: 0; right: 0;
    height: 2px;
    background: var(--rule-grey);
  }
  .band {
    position: absolute;
    left: 0; right: 0;
    background: var(--band-blue);
    color: var(--white);
  }
  .card--front .rule--top { top: 150px; }
  .card--front .band { top: 155px; height: 93px; }
  .card--front .rule--bottom { top: 251px; }
  .card--back .rule--top { top: 152px; }
  .card--back .band { top: 156px; height: 94px; }
  .card--back .rule--bottom { top: 253px; }

  .tagline {
    position: absolute;
    top: 9px; left: 0; right: 0;
    text-align: center;
    font-size: 17px;
  }
  .person { position: absolute; left: 74px; top: 41px; }
  .person__name { font-size: 19px; line-height: 1.2; }
  .person__role { font-size: 14px; margin-top: 2px; }
  .address {
    position: absolute;
    right: 74px; top: 45px;
    text-align: right;
    font-size: 14px;
    line-height: 1.35;
  }
  .mission {
    position: absolute;
    inset: 0;
    display: flex;
    align-items: center;
    justify-content: center;
    text-align: center;
    font-size: 13.4px;
    line-height: 1.42;
    padding: 0 16px;
  }
  .contacts {
    position: absolute;
    left: 0; right: 0;
    text-align: center;
    font-size: 14px;
    line-height: 23px;
    color: var(--ink);
  }
  .card--front .contacts { top: 262px; }
  .card--back .contacts { top: 264px; }
</style>
</head>
<body>
  <section class="card card--front" aria-label="Card front">
    <div class="brand"><span class="brand__mark"></span><span class="brand__name">KORVANEX</span></div>
    <div class="rule rule--top"></div>
    <div class="band">
      <p class="tagline">Where Care Finds Its Pulse</p>
      <div class="person">
        <p class="person__name">Your Name</p>
        <p class="person__role">Designation</p>
      </div>
      <p class="address">123, Abc Street<br>0000 City, Country</p>
    </div>
    <div class="rule rule--bottom"></div>
    <div class="contacts">
      <p>cell : +12 345 67 8910 &nbsp;|&nbsp; phone : +12 345 67 8910</p>
      <p>email : info@yourwebsite.com &nbsp;|&nbsp; web : www.yourwebsite.com</p>
    </div>
  </section>

  <section class="card card--back" aria-label="Card back">
    <div class="brand"><span class="brand__mark"></span><span class="brand__name">KORVANEX</span></div>
    <div class="rule rule--top"></div>
    <div class="band">
      <p class="mission">Korvanex is the leading building services innovator. By combining technology with functional toos that improve efficiency in the workplace, we provide unparalleled service in the industry. Developing lasting relationships with our clients and associates is the cornerstone of our success.</p>
    </div>
    <div class="rule rule--bottom"></div>
    <div class="contacts">
      <p>cell : +12 345 67 8910 &nbsp;|&nbsp; phone : +12 345 67 8910</p>
      <p>email : info@yourwebsite.com &nbsp;|&nbsp; web : www.yourwebsite.com</p>
    </div>
  </section>
</body>
</html>
```